Falkrin homes and renovations business card design.

Would like some new card designs utilizing my new logo that look professional. I am open to different colors on the logo or utilize the same ones we have. I like the original concept but would like to see some fresh ideas and build on what we have already done.

Target Market(s)

Custom home building industry, Real estate sales, Renovation projects.

Industry/Entity Type

Home Builder

Contact Information for Business Card

Falkrin Homes and Renovations
2871 96th Avenue
Wendmoor, Ridgeland
T2R3W8
Home : 403- 718-4063 Cell: 403- 294-5170

My info is : Dax Falkrin, President and CEO
email: falkrinhomes@maildrop-example.net
Website: falkrinhomes-example.com
websit

Requirements
Must have
• Must Use my new logo design. I am open to different colors on the logo or utilize the same ones in the existing design. I can upload the original logo design if needed.

```html
<!DOCTYPE html>
<html lang="en">
<head>
<meta charset="UTF-8">
<title>Falkrin Homes and Renovations — Business Card</title>
<link href="https://fonts.googleapis.com/css2?family=Montserrat:wght@500;600&family=Open+Sans:wght@400;600&display=swap" rel="stylesheet">
<style>
  :root {
    --stage: #d4d4d6;
    --ink: #0c0c0c;
    --paper: #ffffff;
    --gold: #b3873a;
    --gold-bright: #e0a22a;
    --silver: #8a8a8a;
    --text-dark: #1a1a1a;
    --text-light: #f2f2f2;
  }
  * { box-sizing: border-box; margin: 0; padding: 0; }
  html, body { width: 1200px; height: 1200px; overflow: hidden; }
  body {
    background: var(--stage);
    display: flex;
    flex-direction: column;
    align-items: center;
    justify-content: center;
    gap: 56px;
    font-family: "Open Sans", Arial, sans-serif;
  }
  .card {
    position: relative;
    width: 900px;
    height: 514px;
    overflow: hidden;
    box-shadow: 0 10px 24px rgba(0,0,0,0.22);
  }

  /* Back side */
  .card-back {
    background: radial-gradient(ellipse at 50% 40%, #1c1c1c 0%, var(--ink) 70%);
    display: flex;
    flex-direction: column;
    align-items: center;
    justify-content: center;
  }
  .brand-name {
    font-family: "Montserrat", Arial, sans-serif;
    font-weight: 500;
    color: var(--silver);
    text-align: center;
    text-transform: uppercase;
    letter-spacing: 2px;
  }
  .card-back .brand-name { font-size: 30px; line-height: 1.35; margin-top: -20px; }
  .brand-name .line-main { display: block; font-size: 1.6em; letter-spacing: 1px; }
  .card-back .website {
    position: absolute;
    bottom: 92px;
    left: 0; right: 0;
    text-align: center;
    color: var(--gold-bright);
    font-size: 18px;
    letter-spacing: 2px;
  }

  /* Front side */
  .card-front { background: var(--paper); }
  .card-front .shapes { position: absolute; inset: 0; }
  .card-front .brand-name {
    position: absolute;
    left: 56px;
    top: 210px;
    color: var(--gold);
    text-align: left;
    font-size: 17px;
    line-height: 1.3;
  }
  .card-front .brand-name .line-main { font-size: 2.3em; }
  .person {
    position: absolute;
    right: 44px;
    top: 40px;
    text-align: right;
  }
  .person-name { color: var(--gold); font-size: 24px; font-weight: 600; }
  .person-title { color: var(--text-dark); font-size: 17px; }
  .contact {
    position: absolute;
    right: 36px;
    top: 235px;
    text-align: right;
    color: var(--text-light);
    font-size: 16.5px;
    line-height: 1.5;
  }
  .contact .address { margin-bottom: 14px; }
  .contact-row { display: flex; justify-content: flex-end; align-items: center; gap: 10px; }
  .contact-row svg { width: 15px; height: 15px; fill: var(--gold-bright); flex: none; }
</style>
</head>
<body>

  <section class="card card-back" aria-label="Card back">
    <div class="brand-name"><span class="line-main">Falkrin</span>Homes and Renovations</div>
    <div class="website">falkrinhomes-example.com</div>
  </section>

  <section class="card card-front" aria-label="Card front">
    <svg class="shapes" viewBox="0 0 900 514" preserveAspectRatio="none" aria-hidden="true">
      <path d="M900 110 C 680 160, 470 300, 300 514 L 900 514 Z" fill="var(--ink)"/>
      <path d="M620 170 C 470 235, 330 360, 215 514 L 268 514 C 370 370, 480 260, 620 170 Z" fill="var(--gold)"/>
    </svg>

    <div class="brand-name"><span class="line-main">Falkrin</span>Homes and Renovations</div>

    <div class="person">
      <div class="person-name">Dax Falkrin</div>
      <div class="person-title">President &amp;CEO</div>
    </div>

    <div class="contact">
      <div class="address">2871 96th Avenue<br>Wendmoor, Ridgeland, T2R3W8</div>
      <div class="contact-row">403- 718-4063
        <svg viewBox="0 0 24 24"><path d="M6.6 10.8a15 15 0 0 0 6.6 6.6l2.2-2.2c.3-.3.7-.4 1-.2 1.1.4 2.3.6 3.6.6.6 0 1 .4 1 1V20c0 .6-.4 1-1 1C10.6 21 3 13.4 3 4c0-.6.4-1 1-1h3.5c.6 0 1 .4 1 1 0 1.3.2 2.5.6 3.6.1.3 0 .7-.2 1z"/></svg>
      </div>
      <div class="contact-row">403- 294-5170
        <svg viewBox="0 0 24 24"><path d="M7 2h10a2 2 0 0 1 2 2v16a2 2 0 0 1-2 2H7a2 2 0 0 1-2-2V4a2 2 0 0 1 2-2zm0 3v13h10V5zm5 14.2a1 1 0 1 0 0 .1z"/></svg>
      </div>
      <div class="contact-row">falkrinhomes@maildrop-example.net
        <svg viewBox="0 0 24 24"><path d="M3 5h18v14H3zm2 2v.5l7 4.5 7-4.5V7zm0 2.8V17h14V9.8l-7 4.5z"/></svg>
      </div>
      <div class="contact-row">falkrinhomes-example.com
        <svg viewBox="0 0 24 24"><path d="M12 2a10 10 0 1 0 0 20 10 10 0 0 0 0-20zm6.9 9h-3a15 15 0 0 0-1.3-5.6A8 8 0 0 1 18.9 11zM12 4.1c.9 1.2 1.7 3.6 1.9 6.9h-3.8c.2-3.3 1-5.700 1.9-6.9zM9.4 5.4A15 15 0 0 0 8.1 11h-3a8 8 0 0 1 4.3-5.6zM5.1 13h3a15 15 0 0 0 1.3 5.6A8 8 0 0 1 5.1 13zm6.9 6.9c-.9-1.2-1.7-3.6-1.9-6.9h3.8c-.2 3.3-1 5.7-1.9 6.9zm2.6-1.3a15 15 0 0 0 1.3-5.6h3a8 8 0 0 1-4.3 5.6z"/></svg>
      </div>
    </div>
  </section>

</body>
</html>
```